Dalvick's Business Card

I need some designs for a new business card including the new logo attached. An old example of our business card is also attached to show all the data that should be included on the new design.
**I added some more examples someone had mocked up**

Contact Information for Business Card

Should include all info on other examples uploaded.

```html
<!DOCTYPE html>
<html lang="en">
<head>
<meta charset="utf-8">
<title>Dalvick's Business Card</title>
<link href="https://fonts.googleapis.com/css2?family=Montserrat:wght@400;500;600;700&display=swap" rel="stylesheet">
<style>
  :root {
    --backdrop: #acacac;
    --card-white: #ffffff;
    --brand-red: #c0283f;
    --brand-purple: #5a4d8c;
    --brand-blue: #0371bd;
    --text-gray: #6f6f6f;
    --rule-gray: #d4d4d4;
    --badge-gray: #dcdcdc;
    --icon-red: #e4262f;
  }
  * { margin: 0; padding: 0; box-sizing: border-box; }
  html, body { width: 1200px; height: 1000px; overflow: hidden; }
  body {
    background: var(--backdrop);
    font-family: "Montserrat", sans-serif;
    position: relative;
  }
  .card {
    position: absolute;
    left: 294px;
    width: 613px;
    height: 352px;
    border-radius: 24px;
    overflow: hidden;
  }
  .card-front { top: 96px; }
  .card-back { top: 528px; background: var(--card-white); }

  .front-pattern {
    position: absolute; inset: 0;
    background: linear-gradient(90deg, var(--brand-red) 0%, var(--brand-purple) 45%, var(--brand-blue) 75%, var(--brand-blue) 100%);
  }
  .front-title {
    position: absolute;
    left: 0; right: 0;
    top: 128px;
    text-align: center;
    color: #fff;
  }
  .front-title .company-name {
    display: block;
    font-size: 68px;
    font-weight: 500;
    letter-spacing: 1px;
    line-height: 1;
  }
  .front-title .company-tagline {
    display: block;
    margin-top: 4px;
    font-size: 15.5px;
    font-weight: 600;
    letter-spacing: 0.2px;
  }

  .back-brand {
    position: absolute;
    left: 39px;
    top: 56px;
    display: flex;
    align-items: center;
    gap: 8px;
    color: var(--brand-blue);
    font-size: 26px;
    font-weight: 700;
  }
  .back-brand .brand-dot {
    width: 14px; height: 14px;
    border-radius: 50%;
    background: var(--brand-red);
  }
  .back-badge {
    position: absolute;
    left: 403px;
    top: 2px;
    width: 210px;
    height: 210px;
  }
  .contact-name {
    position: absolute;
    left: 39px;
    top: 218px;
    color: var(--brand-blue);
    font-size: 21px;
    font-weight: 500;
  }
  .name-rule {
    position: absolute;
    left: 39px;
    top: 256px;
    width: 146px;
    height: 2px;
    background: var(--rule-gray);
  }
  .contact-block {
    position: absolute;
    top: 273px;
    color: var(--text-gray);
    font-size: 17px;
    line-height: 21px;
    letter-spacing: 0.4px;
  }
  .contact-address { left: 38px; }
  .contact-lines { left: 334px; }
  .contact-lines .line { display: flex; align-items: center; gap: 6px; }
  .contact-lines svg { flex: none; }
</style>
</head>
<body>
  <section class="card card-front" aria-label="Card front">
    <div class="front-pattern" role="img" aria-label="Red-to-blue gradient with repeating brand mark pattern"></div>
    <div class="front-title">
      <span class="company-name">DALVICK'S</span>
      <span class="company-tagline">AIR CONDITIONING &amp; HEATING SERVICE</span>
    </div>
  </section>

  <section class="card card-back" aria-label="Card back">
    <div class="back-brand">
      <span class="brand-dot"></span>
      <span>DALVICK'S</span>
    </div>
    <svg class="back-badge" viewBox="0 0 210 210" role="img" aria-label="Licensed and insured, family owned seal">
      <circle cx="105" cy="105" r="100" fill="none" stroke="var(--badge-gray)" stroke-width="3"/>
      <circle cx="105" cy="105" r="62" fill="var(--badge-gray)" opacity="0.6"/>
    </svg>
    <div class="contact-name">Reid Dalvick</div>
    <div class="name-rule"></div>
    <div class="contact-block contact-address">
      <div>418 Birchmont Avenue</div>
      <div>Cedarvale, IA 51620, EUA</div>
    </div>
    <div class="contact-block contact-lines">
      <div class="line">
        <svg width="11" height="11" viewBox="0 0 24 24" aria-hidden="true"><path fill="var(--icon-red)" d="M6.6 10.8a15.1 15.1 0 0 0 6.6 6.6l2.2-2.2a1 1 0 0 1 1-.25 11.4 11.4 0 0 0 3.6.57 1 1 0 0 1 1 1V20a1 1 0 0 1-1 1A17 17 0 0 1 3 4a1 1 0 0 1 1-1h3.5a1 1 0 0 1 1 1c0 1.25.2 2.45.57 3.6a1 1 0 0 1-.25 1z"/></svg>
        <span>555.014.2287</span>
      </div>
      <div class="line">
        <svg width="12" height="10" viewBox="0 0 24 18" aria-hidden="true"><rect width="24" height="18" fill="var(--icon-red)"/><path d="M1 1l11 9 11-9" fill="none" stroke="#fff" stroke-width="2"/></svg>
        <span>hvacdalvick@example.com</span>
      </div>
    </div>
  </section>
</body>
</html>
```